we can communicate on this, but i want to follow the approach we took on Pellew|Marsh & Quinlan but i feel the card front needs the black background and the platinum and gold logo. The back? I am open. we can use the same info from PM&Q. Velmont Arc is an enhanced equity investment fund - basically a very exclusive boutique hedge fund that uses only stock options. very advanced things. hope you are interested

Contact Information for Business Card

Dr. Lewis T. Brennick, CFA
Scientifique de fusée financière
701.555.0143
LTBquant47@mailvantor.com

4718 Willow Creek Bend W.
West Fargo, ND 58078

No web site

Colors

Designer to choose colors to be used in the design.

Requirements
Nice to have
• I tend to prefer the most visible applications of the logo to include logo and name, the logo version with a black background and the gold and platinum components separated by the black. I see this working well for a single side (logo and name - this is card front to me).
• I am fairly open to other treatments on the reverse side with the data. To me, it makes sense to have a different color rendition of the logo on the reverse and it may be a muted black tone on tone or an oversized portion that would have spot UV. Or, the reverse may play with colors and layout
Should not have
• Other colors = no no
• Decorative font

```html
<!DOCTYPE html>
<html lang="en">
<head>
<meta charset="utf-8">
<title>Velmont Arc — Business Cards</title>
<link href="https://fonts.googleapis.com/css2?family=Montserrat:wght@400;600;700&display=swap" rel="stylesheet">
<style>
  :root {
    --stage: #2b2b2b;
    --card-black: #050505;
    --card-back: #0d0d0d;
    --gold-light: #f1d27a;
    --gold: #c9a23c;
    --gold-deep: #a27c22;
    --white: #ffffff;
    --ink: #1a1a1a;
  }
  * { box-sizing: border-box; margin: 0; padding: 0; }
  html, body { width: 1200px; height: 1108px; overflow: hidden; }
  body {
    background: var(--stage);
    font-family: "Montserrat", sans-serif;
    position: relative;
  }
  .card {
    position: absolute;
    top: 190px;
    width: 400px;
    height: 700px;
    border-radius: 26px;
    overflow: hidden;
    background: var(--card-black);
  }
  .card--front { left: 150px; }
  .card--back { left: 650px; background: var(--card-back); }

  .brand {
    position: absolute;
    left: 0; right: 0;
    text-align: center;
  }
  .brand__mark {
    display: block;
    margin: 0 auto 22px;
    width: 120px; height: 120px;
    border-radius: 50%;
    background: var(--gold);
  }
  .brand__name {
    color: var(--white);
    font-weight: 700;
    font-size: 40px;
    letter-spacing: 2px;
    text-transform: uppercase;
  }
  .card--front .brand { top: 95px; }
  .card--back .brand { top: 240px; }

  .person {
    position: absolute;
    top: 335px; left: 20px; right: 20px;
    text-align: center;
  }
  .person__name {
    color: var(--white);
    font-weight: 700;
    font-size: 21px;
    letter-spacing: 1px;
    text-transform: uppercase;
  }
  .person__title {
    color: var(--gold);
    font-weight: 400;
    font-size: 16px;
    margin-top: 4px;
  }

  .contact {
    position: absolute;
    left: 40px; right: 40px;
    text-align: center;
    color: var(--white);
    font-size: 18px;
  }
  .contact__rule {
    display: flex;
    align-items: center;
    gap: 8px;
    margin-bottom: 8px;
  }
  .contact__rule::before, .contact__rule::after {
    content: "";
    flex: 1;
    height: 2px;
    background: linear-gradient(90deg, transparent, var(--gold), transparent);
  }
  .contact__icon {
    width: 34px; height: 34px;
    border-radius: 50%;
    border: 2px solid var(--gold-light);
    background: var(--gold);
    display: flex; align-items: center; justify-content: center;
  }
  .contact--phone { top: 425px; }
  .contact--email { top: 505px; }

  .gold-band {
    position: absolute;
    left: 0; right: 0; bottom: 0;
    height: 78px;
    border-top: 4px solid var(--white);
    box-shadow: 0 -6px 0 var(--card-black);
    background: linear-gradient(90deg, var(--gold-deep), var(--gold-light) 40%, var(--gold) 75%, var(--gold-deep));
    display: flex; flex-direction: column; align-items: center; justify-content: center;
    color: var(--ink);
    text-align: center;
  }
  .card--back .gold-band { box-shadow: 0 -6px 0 var(--card-back); }
  .address__line {
    font-size: 16px;
    font-weight: 600;
    letter-spacing: 0.5px;
    line-height: 1.35;
  }
</style>
</head>
<body>

  <section class="card card--front" aria-label="Card front">
    <div class="brand">
      <span class="brand__mark"></span>
      <div class="brand__name">Velmont Arc</div>
    </div>

    <div class="person">
      <div class="person__name">Dr. Lewis T. Brennick, CFA</div>
      <div class="person__title">Scientifique de fusée financière</div>
    </div>

    <div class="contact contact--phone">
      <div class="contact__rule">
        <span class="contact__icon">
          <svg width="16" height="16" viewBox="0 0 24 24" aria-hidden="true">
            <path d="M6.6 10.8a15 15 0 0 0 6.6 6.6l2.2-2.2a1 1 0 0 1 1-.25 11.4 11.4 0 0 0 3.6.57 1 1 0 0 1 1 1V20a1 1 0 0 1-1 1A17 17 0 0 1 3 4a1 1 0 0 1 1-1h3.5a1 1 0 0 1 1 1c0 1.25.2 2.45.57 3.6a1 1 0 0 1-.25 1z" fill="#111"/>
          </svg>
        </span>
      </div>
      <div>701.555.0143</div>
    </div>

    <div class="contact contact--email">
      <div class="contact__rule">
        <span class="contact__icon">
          <svg width="16" height="16" viewBox="0 0 24 24" aria-hidden="true">
            <rect x="3" y="6" width="18" height="12" rx="1" fill="none" stroke="#111" stroke-width="2"/>
            <path d="M3 7l9 6 9-6" fill="none" stroke="#111" stroke-width="2"/>
          </svg>
        </span>
      </div>
      <div>LTBquant47@mailvantor.com</div>
    </div>

    <address class="gold-band address" style="font-style: normal;">
      <span class="address__line">4718 Willow Creek Bend W.</span>
      <span class="address__line">West Fargo, ND 58078</span>
    </address>
  </section>

  <section class="card card--back" aria-label="Card back">
    <div class="brand">
      <span class="brand__mark"></span>
      <div class="brand__name">Velmont Arc</div>
    </div>
    <div class="gold-band"></div>
  </section>

</body>
</html>
```